Menu Design Project

Menu design for a Japanese fast food restaurant featuring Teppanyaki and Sushi. The restaurant main scene color is black and wood color. No Japan scenery pictures. Menu try to be simply and elegant . Pictures provided can be used accordingly to the menu items, but doesn't have to be due to the back ground color of the picture is white.

Target Market(s)

Young and progressive consumers

Industry/Entity Type

Asian Restaurant

Font styles to use
Other font styles liked:
• Han Wang Kan Tan Font

Colors
1b1b1b
fee18a

Requirements
Must have
• Pictures of the Sushi that is provided, and all the item in the Word file.
Nice to have
• Keep it simple but different
Should not have
• No scenery pictures, no cherry blossom.

```html
<!DOCTYPE html>
<html lang="en">
<head>
<meta charset="utf-8">
<title>Sushi &amp; Teppanyaki Menu</title>
<link rel="stylesheet" href="https://fonts.googleapis.com/css2?family=Francois+One&family=Open+Sans:wght@400;600;700&display=swap">
<style>
:root{
  --ink:#1b1b1b;
  --gold:#fee18a;
  --paper:#f2d982;
  --text:#f4f4f4;
  --muted:#d8d8d8;
  --stage:#9a9a9a;
  --rice:#efe9dc;
  --fish:#e9a08a;
}
*{box-sizing:border-box;margin:0;padding:0}
html,body{width:1200px;height:864px;overflow:hidden}
body{background:var(--stage);font-family:"Open Sans",Arial,sans-serif;color:var(--text)}
.brochure{position:absolute;left:24px;top:14px;width:1152px;height:836px;display:flex;box-shadow:0 10px 30px rgba(0,0,0,.35)}
.panel{position:relative;width:384px;height:100%;overflow:hidden;background:var(--ink)}
.photo{position:absolute;border-radius:10px}
.deco{position:absolute;inset:0;width:100%;height:100%}

/* left panel */
.panel--left{background:var(--paper)}
.band{position:absolute;left:0;right:0;background:var(--ink)}
.band--top{top:22px;height:88px}
.band--entree{top:158px;height:262px;padding:12px 18px}
.band--sushi{top:468px;height:346px;padding:10px 18px}
.section-bar{position:absolute;left:0;right:0;height:48px;display:flex;align-items:center;justify-content:center;
  font-family:"Francois One",Impact,sans-serif;font-size:30px;letter-spacing:2px;color:var(--ink)}
.section-bar--entree{top:110px}
.section-bar--sushi{top:420px}
.note{font-size:11px;color:var(--muted);text-align:right;line-height:1.3}
.note b{color:var(--text)}
.entree-list{list-style:none;margin-top:6px;font-size:11px;line-height:14.4px}
.entree-list li{display:flex;justify-content:space-between}
.sub-head{font-size:12px;font-weight:700;margin:6px 0 6px}

/* menu items */
.item{display:flex;justify-content:space-between;align-items:center;gap:8px}
.item__text{flex:1}
.item__name{font-weight:700;font-size:12.5px;letter-spacing:.3px;text-transform:uppercase;line-height:1.2}
.item__desc{font-size:10.5px;line-height:1.25;color:var(--muted)}
.item__thumb{width:64px;height:22px;border-radius:5px;background:linear-gradient(90deg,#e98a63,#f6f0e2,#7fa55a)}
.item__thumb--small{width:26px;height:26px;border-radius:5px;background:linear-gradient(135deg,var(--rice),var(--fish))}
.item__price{font-size:11px;font-weight:700;white-space:nowrap;min-width:46px;text-align:right}
.item__price--pcs{min-width:118px}
.special-list{display:flex;flex-direction:column;gap:10px}

/* middle panel */
.roll-list{position:absolute;left:22px;right:18px;top:232px;display:flex;flex-direction:column;gap:7px}
.mid-sub{margin-top:14px;font-size:12px;font-weight:700;letter-spacing:.5px}

/* right panel */
.right-list{position:absolute;left:20px;right:18px;top:190px;display:flex;flex-direction:column;gap:6px}
.addon{margin-top:14px;font-size:12.5px;font-weight:700;line-height:1.35;text-transform:uppercase}
</style>
</head>
<body>
<main class="brochure">

  <section class="panel panel--left">
    <div class="band band--top">
      <div class="photo" role="img" aria-label="Crab stick nigiri sushi" style="left:40px;top:8px;width:200px;height:72px;background:linear-gradient(90deg,#e7694a,#f3b59c 60%,#f4efe4)"></div>
    </div>
    <h2 class="section-bar section-bar--entree">ENTREE</h2>
    <div class="band band--entree">
      <p class="note">with Hibachi Vegetable and Fried Rice, or Yakisoba Noodle<br>add <b>$0.99</b></p>
      <ul class="entree-list">
        <li><span>Teriyaki Chicken (double Chicken Special $1.59)</span><span>$6.89</span></li>
        <li><span>Teriyaki Beef</span><span>$7.29</span></li>
        <li><span>Teriyaki Shrimp</span><span>$7.89</span></li>
        <li><span>Teriyaki Chicken &amp; Shrimp</span><span>$8.89</span></li>
        <li><span>Teriyaki Chicken &amp; Beef</span><span>$8.49</span></li>
        <li><span>Teriyaki Beef &amp; Shrimp</span><span>$9.29</span></li>
        <li><span>Teriyaki Chicken Beef &amp; Shrimp</span><span>$10.29</span></li>
        <li><span>Hibachi Chicken</span><span>$7.59</span></li>
        <li><span>Hibachi Beef</span><span>$7.99</span></li>
        <li><span>Hibachi Shrimp</span><span>$8.59</span></li>
        <li><span>Hibachi Chicken &amp; Shrimp</span><span>$9.59</span></li>
        <li><span>Hibachi Chicken &amp; Beef</span><span>$9.19</span></li>
        <li><span>Hibachi Beef &amp; Shrimp</span><span>$9.99</span></li>
        <li><span>Hibachi Chicken, Beef &amp; Shrimp</span><span>$10.99</span></li>
      </ul>
    </div>
    <h2 class="section-bar section-bar--sushi">SUSHI</h2>
    <div class="band band--sushi">
      <p class="note" style="text-align:center">Ingredients subject to availability</p>
      <h3 class="sub-head">SPECIAL ROLL</h3>
      <div class="special-list">
        <div class="item"><div class="item__text"><p class="item__name">Dragon Roll</p><p class="item__desc">Grilled Eel fish &amp; cucumber top with avocado &amp; Unagi sauce</p></div><div class="item__thumb" role="img" aria-label="Dragon roll"></div><span class="item__price">$9.99</span></div>
        <div class="item"><div class="item__text"><p class="item__name">Deluxe Black Dragon Roll</p><p class="item__desc">Tempura Shrimp top with Avocado, Grilled Eel fish &amp; Unagi sauce</p></div><span class="item__price">$11.99</span></div>
        <div class="item"><div class="item__text"><p class="item__name">Rainbow Roll</p><p class="item__desc">avocado, cucumber &amp; Kani top with red snapper, tuna, salmon &amp; avocado</p></div><div class="item__thumb" role="img" aria-label="Rainbow roll"></div><span class="item__price">$10.99</span></div>
        <div class="item"><div class="item__text"><p class="item__name">Four Season Roll</p><p class="item__desc">Tuna, salmon, oshinko</p></div><span class="item__price">$9.99</span></div>
        <div class="item"><div class="item__text"><p class="item__name">Deluxe Philly Roll</p><p class="item__desc">Salmon, cream cheese &amp; avocado top with more salmon</p></div><span class="item__price">$9.99</span></div>
      </div>
    </div>
  </section>

  <section class="panel panel--middle">
    <svg class="deco" viewBox="0 0 384 836" preserveAspectRatio="none" aria-hidden="true">
      <polygon points="0,0 384,0 384,110 300,170 80,170 0,230" fill="var(--paper)"/>
      <polygon points="0,800 384,780 384,836 0,836" fill="var(--paper)"/>
    </svg>
    <div class="photo" role="img" aria-label="Shrimp tempura" style="left:100px;top:36px;width:180px;height:114px;background:linear-gradient(135deg,#f1cf56,#d9a83a)"></div>
    <div class="roll-list">
      <div class="item"><div class="item__text"><p class="item__name">Massago Roll</p><p class="item__desc">Kani crab meat, cucumber &amp; avocado top with Premium Massago Roe</p></div><div class="item__thumb" role="img" aria-label="Massago roll"></div><span class="item__price">$8.99</span></div>
      <div class="item"><div class="item__text"><p class="item__name">Deluxe Spicy Tuna Roll</p><p class="item__desc">Kani crab meat, Cucumber &amp; avocado top with Spicy grounded tuna</p></div><div class="item__thumb" role="img" aria-label="Spicy tuna roll"></div><span class="item__price">$9.49</span></div>
      <div class="item"><div class="item__text"><p class="item__name">Deluxe Spicy Kani Roll</p><p class="item__desc">Kani crab meat, cucumber &amp; avocado top with seasoned ground Crab meat</p></div><div class="item__thumb" role="img" aria-label="Spicy kani roll"></div><span class="item__price">$9.49</span></div>
      <div class="item"><div class="item__text"><p class="item__name">Deluxe Kani Roll</p><p class="item__desc">Kani crab meat, cucumber &amp; avocado top with Kani &amp; Panko crumb</p></div><div class="item__thumb" role="img" aria-label="Kani roll"></div><span class="item__price">$9.49</span></div>
      <div class="item"><div class="item__text"><p class="item__name">Tri Deluxe Fish Roll</p><p class="item__desc">Tuna, salmon &amp; red snapper</p></div><div class="item__thumb item__thumb--small" role="img" aria-label="Fish roll"></div><span class="item__price">$9.99</span></div>
      <div class="item"><div class="item__text"><p class="item__name">Sumo Roll</p><p class="item__desc">Tuna, Salmon, White Tuan, Red snapper Avocado &amp; Kani Crab Meat</p></div><span class="item__price">$10.99</span></div>
      <div class="item"><div class="item__text"><p class="item__name">Hamachi Asparagus Roll</p><p class="item__desc">Hamachi, Scallion &amp; Asparagus with Ponzu Sauce</p></div><span class="item__price">$7.99</span></div>
      <h3 class="mid-sub">REGULAR MAKI ROLL</h3>
      <div class="item"><div class="item__text"><p class="item__name">Salmon Roll</p><p class="item__desc">salmon &amp; avocado</p></div><div class="item__thumb item__thumb--small" role="img" aria-label="Salmon roll"></div><span class="item__price item__price--pcs">(8pcs) $5.49 (12pcs) $7.49</span></div>
      <div class="item"><div class="item__text"><p class="item__name">Tuna Roll</p><p class="item__desc">tuna &amp; avocado</p></div><div class="item__thumb item__thumb--small" role="img" aria-label="Tuna roll"></div><span class="item__price item__price--pcs">(8pcs) $5.49 (12pcs) $7.49</span></div>
      <div class="item"><div class="item__text"><p class="item__name">Philly Roll</p><p class="item__desc">salmon, cream cheese &amp; avocado</p></div><span class="item__price item__price--pcs">(8pcs) $5.49 (12pcs) $7.49</span></div>
      <div class="item"><div class="item__text"><p class="item__name">California Roll</p><p class="item__desc">cucumber, avocado &amp; kani crab meat</p></div><span class="item__price item__price--pcs">(8pcs) $5.49 (12pcs) $7.49</span></div>
    </div>
    <div class="photo" role="img" aria-label="Row of sashimi rosettes with wasabi" style="left:40px;top:760px;width:300px;height:56px;background:linear-gradient(90deg,#a9c46a,#f0a57c 25%,#ea7d8d 45%,#f2c9b4 65%,#f4ead2)"></div>
  </section>

  <section class="panel panel--right">
    <svg class="deco" viewBox="0 0 384 836" preserveAspectRatio="none" aria-hidden="true">
      <polygon points="160,0 384,0 384,120" fill="var(--paper)"/>
      <polygon points="90,600 384,560 384,836 0,836 0,760" fill="var(--paper)"/>
    </svg>
    <div class="photo" role="img" aria-label="Tuna, yellowtail and salmon nigiri" style="left:30px;top:40px;width:330px;height:110px;background:linear-gradient(100deg,#d23a4a,#f2d8cf 45%,#f19a74 75%,#f3b08d)"></div>
    <div class="right-list">
      <div class="item"><div class="item__text"><p class="item__name">Kani &amp; Cheese Roll</p><p class="item__desc">Kani crab meat &amp; cream cheese</p></div><span class="item__price item__price--pcs">(8pcs) $5.49 (12pcs) $7.49</span></div>
      <div class="item"><div class="item__text"><p class="item__name">Shrimp Tempura Roll</p><p class="item__desc">Fried tempura shrimp &amp; cucumber</p></div><span class="item__price item__price--pcs">(8pcs) $6.49</span></div>
      <div class="item"><div class="item__text"><p class="item__name">Alaska Roll</p><p class="item__desc">Salmon &amp; avocado with massago</p></div><span class="item__price item__price--pcs">(8pcs) $5.49 (12pcs) $7.49</span></div>
      <div class="item"><div class="item__text"><p class="item__name">Grilled Eel Roll</p><p class="item__desc">Eel &amp; avocado</p></div><span class="item__price item__price--pcs">(8pcs) $5.49 (12pcs) $7.49</span></div>
      <div class="item"><div class="item__text"><p class="item__name">Spicy Tuna Roll</p><p class="item__desc">seasoned ground tuna</p></div><span class="item__price item__price--pcs">(8pcs) $5.49 (12pcs) $7.49</span></div>
      <div class="item"><div class="item__text"><p class="item__name">Spicy Salmon Roll</p><p class="item__desc">seasoned ground salmon</p></div><span class="item__price item__price--pcs">(8pcs) $5.49 (12pcs) $7.49</span></div>
      <div class="item"><div class="item__text"><p class="item__name">Spicy Kani Roll</p><p class="item__desc">seasoned ground crab meat</p></div><span class="item__price item__price--pcs">(8pcs) $4.49 (16pcs) $7.99</span></div>
      <div class="item"><div class="item__text"><p class="item__name">Vegetarian Roll</p><p class="item__desc">avocado, cucumber</p></div></div>
      <p class="addon">Add Ajitsuke seasoned fried bean curd<br>for $1.00 more</p>
    </div>
    <div class="photo" role="img" aria-label="Close-up of a cut maki roll with tuna, kani and avocado" style="left:120px;top:570px;width:210px;height:210px;border-radius:16px;background:linear-gradient(135deg,#f4efe6 0%,#e8c8bd 45%,#d9d0b8 75%,#ece6d8 100%)"></div>
  </section>

</main>
</body>
</html>
```